DOUBLE SIDED BROCHURE NEEDED TO PROMOTE DOCTOR

I need a double sided DL size (99mm x 210mm) brochure, promoting a doctor seeing patients in a new area.

I want something professional. I have included the relevant information. I would also like the Dr's picture somwhere in the brochure, with a professional background. I wish to print these tomorrow, so i will pick a winner within 14 hours of posting this ad.

I have included an example of a brochures design that I recently saw, and its definietly a good starting point.

Industry/Entity Type

Medical

```html
<!DOCTYPE html>
<html lang="en">
<head>
<meta charset="utf-8">
<title>Referral Card – Dr. Elias Marwen</title>
<link href="https://fonts.googleapis.com/css2?family=Mulish:wght@600;800&display=swap" rel="stylesheet">
<style>
  :root {
    --stage: #e9e9e9;
    --card-orange: #f27a3c;
    --panel-light: #f1914c;
    --panel-deep: #fb6a10;
    --accent-lime: #c9c81f;
    --heart-red: #b3121a;
    --heart-glow: #f8a07a;
    --ink-light: #ffffff;
  }
  html, body {
    margin: 0;
    width: 1200px;
    height: 1200px;
    overflow: hidden;
    background: var(--stage);
  }
  .canvas {
    position: relative;
    width: 1200px;
    height: 1200px;
  }
  .referral-card {
    position: absolute;
    left: 340px;
    top: 50px;
    width: 520px;
    height: 1100px;
    overflow: hidden;
    background: var(--card-orange);
    font-family: "Mulish", sans-serif;
    color: var(--ink-light);
  }
  .card-shapes {
    position: absolute;
    inset: 0;
  }
  .heart-artwork {
    position: absolute;
    left: 286px;
    top: 37px;
    width: 186px;
    height: 130px;
    border-radius: 50%;
    background: radial-gradient(ellipse at 50% 50%, var(--heart-red) 0%, #d8322c 45%, var(--heart-glow) 72%, rgba(248,160,122,0) 100%);
  }
  .letter {
    position: absolute;
    left: 11px;
    top: 134px;
    width: 505px;
    font-weight: 800;
    font-size: 26.5px;
    line-height: 35.5px;
    letter-spacing: -0.2px;
    text-shadow: 0 1px 2px rgba(120, 30, 10, 0.55);
  }
  .letter p { margin: 0 0 35.5px; }
  .contact-list {
    position: absolute;
    left: 0;
    top: 676px;
    width: 520px;
    margin: 0;
    padding: 0;
    list-style: none;
    font-weight: 600;
    font-size: 30px;
    line-height: 39.5px;
  }
  .contact-item {
    position: relative;
    padding-left: 80px;
    margin-bottom: 42px;
  }
  .contact-icon {
    position: absolute;
    fill: var(--ink-light);
  }
  .icon-pin { left: 18px; top: 8px; width: 38px; height: 54px; }
  .icon-phone { left: 14px; top: 2px; width: 44px; height: 54px; }
  .icon-fax { left: 6px; top: 4px; width: 56px; height: 46px; }
</style>
</head>
<body>
<main class="canvas">
  <article class="referral-card">
    <svg class="card-shapes" viewBox="0 0 520 1100" width="520" height="1100" aria-hidden="true">
      <defs>
        <linearGradient id="panelFill" x1="0" y1="0" x2="1" y2="0">
          <stop offset="0" stop-color="var(--panel-light)"/>
          <stop offset="1" stop-color="var(--panel-deep)"/>
        </linearGradient>
        <linearGradient id="edgeStroke" x1="0" y1="0" x2="1" y2="0">
          <stop offset="0" stop-color="#ffffff" stop-opacity="0.9"/>
          <stop offset="0.55" stop-color="#f6e6a0"/>
          <stop offset="1" stop-color="var(--accent-lime)"/>
        </linearGradient>
      </defs>
      <path class="contact-panel" d="M0,594 Q300,570 520,752 L520,993 Q440,1068 323,1100 L0,1100 Z" fill="url(#panelFill)"/>
      <path d="M0,594 Q300,570 520,752" fill="none" stroke="url(#edgeStroke)" stroke-width="4"/>
      <path d="M520,993 Q440,1068 323,1100" fill="none" stroke="var(--accent-lime)" stroke-width="4"/>
    </svg>

    <div class="heart-artwork" role="img" aria-label="Illustration of two glossy red hearts"></div>

    <section class="letter">
      <p>Dear Doctors,</p>
      <p>We are pleased to announce that Dr. Elias Marwen is now consulting in Harbourvale, seeing public and private patients.</p>
      <p>Guaranteed appointment within two weeks, with patients having the option of surgery at Coastal Health Campus, Westbrook General Hospital or St. Anselm Bayside.</p>
    </section>

    <ul class="contact-list">
      <li class="contact-item">
        <svg class="contact-icon icon-pin" viewBox="0 0 38 54" aria-hidden="true">
          <path d="M19 0C8.5 0 0 8.3 0 18.6 0 32 19 54 19 54S38 32 38 18.6C38 8.3 29.5 0 19 0Zm0 26a7.5 7.5 0 1 1 0-15 7.5 7.5 0 0 1 0 15Z"/>
        </svg>
        Harbourvale Clinic:<br>42 Tidewater Road<br>Harbourvale WA 6999.
      </li>
      <li class="contact-item">
        <svg class="contact-icon icon-phone" viewBox="0 0 44 54" aria-hidden="true">
          <path d="M9 2 3 6C-1 10 0 22 8 35s19 20 25 19l6-4c2-1.5 2.5-3.5 1-5.5l-6-8c-1.3-1.8-3.5-2-5-1l-4 2.5C21 35 14 24 14.5 20.5l4-2.5c1.6-1 2-3.2 1-5L14 3C12.8 1 10.8.8 9 2Z"/>
        </svg>
        Phone: 1300 000 123
      </li>
      <li class="contact-item">
        <svg class="contact-icon icon-fax" viewBox="0 0 56 46" aria-hidden="true">
          <rect x="0" y="14" width="12" height="32" rx="3"/>
          <rect x="18" y="0" width="26" height="16"/>
          <path d="M15 14h38a3 3 0 0 1 3 3v26a3 3 0 0 1-3 3H15Z"/>
          <rect x="22" y="4" width="18" height="2" fill="var(--card-orange)"/>
          <rect x="22" y="9" width="18" height="2" fill="var(--card-orange)"/>
          <rect x="21" y="22" width="26" height="5" fill="var(--card-orange)"/>
          <rect x="21" y="32" width="5" height="4" fill="var(--card-orange)"/>
          <rect x="30" y="32" width="5" height="4" fill="var(--card-orange)"/>
          <rect x="39" y="32" width="5" height="4" fill="var(--card-orange)"/>
        </svg>
        Please send all referrals by<br>fax to (08) 5550 0142.
      </li>
    </ul>
  </article>
</main>
</body>
</html>
```